RTavenor Business Cards & Letterhead

I have a logo but need a design for some new business cards. We are a Design-Build Firm that specializes in the design and construction of commercial projects.
the cards need to be professional. no cartoon stuff.
i would like to have the cards in AI format so I can update the card as needed. Logo is provided.
Our Address is: 4187 Marlowe Ct. Linwood, Vermont 27614

```html
<!DOCTYPE html>
<html lang="en">
<head>
<meta charset="utf-8">
<title>RTavenor Stationery</title>
<link href="https://fonts.googleapis.com/css2?family=Lato:wght@400;700;900&family=Open+Sans:wght@400;600;700&family=Great+Vibes&display=swap" rel="stylesheet">
<style>
  :root{
    --brand-blue:#0866a0;
    --brand-grey:#6d6e71;
    --ink:#231f20;
    --paper:#ffffff;
    --backdrop:#e8e5e0;
  }
  *{margin:0;padding:0;box-sizing:border-box}
  html,body{width:1200px;height:942px;overflow:hidden}
  body{background:var(--backdrop);position:relative;font-family:"Lato",sans-serif;color:var(--ink)}

  .letterhead{position:absolute;left:84px;top:89px;width:541px;height:765px;background:var(--paper);box-shadow:0 2px 8px rgba(0,0,0,.25);overflow:hidden}
  .wordmark{font-family:"Lato",sans-serif;font-weight:900;color:var(--brand-grey);letter-spacing:.5px;display:flex;align-items:center;line-height:1;white-space:nowrap}
  .wordmark .mark-square{background:var(--brand-blue);display:inline-block;flex:none}
  .letterhead .wordmark{position:absolute;left:27px;top:54px;font-size:35px;gap:6px}
  .letterhead .wordmark .mark-square{width:25px;height:25px}

  .lh-contact{position:absolute;left:388px;top:38px;height:62px;border-left:1.5px solid var(--brand-blue);padding-left:10px;font-family:"Open Sans",sans-serif;font-size:10px;line-height:12px;color:var(--ink)}
  .lh-contact .address{margin-bottom:7px}
  .contact-row{display:flex;align-items:center;gap:3px;white-space:nowrap}
  .icon{fill:var(--brand-blue);flex:none}

  .letter{position:absolute;left:27px;top:175px;width:488px;font-size:11px;line-height:12px}
  .letter .date{margin-bottom:14px}
  .letter .recipient{margin-bottom:13px}
  .letter .salutation{font-weight:700;font-size:13.5px;margin:11px 0 15px}
  .letter p.body-copy{text-align:justify;margin-bottom:12px;letter-spacing:-.05px}
  .letter .closing{margin-top:27px}
  .signature{position:absolute;left:27px;top:612px;font-family:"Great Vibes",cursive;font-size:26px;color:var(--ink)}

  .footer-band{position:absolute;left:0;right:0;bottom:0;background:var(--brand-blue)}
  .footer-rule{position:absolute;left:0;right:0;background:var(--brand-grey)}
  .letterhead .footer-band{height:36px}
  .letterhead .footer-rule{bottom:42px;height:3px}

  .card{position:absolute;left:673px;width:444px;height:255px;background:var(--paper);border-radius:18px;box-shadow:0 3px 8px rgba(0,0,0,.3);overflow:hidden}
  .card-front{top:201px}
  .card-front .wordmark{position:absolute;left:36px;top:102px;font-size:57px;gap:9px}
  .card-front .wordmark .mark-square{width:41px;height:41px}
  .card-back{top:488px}
  .card-back .wordmark{position:absolute;left:33px;top:115px;font-size:29px;gap:5px}
  .card-back .wordmark .mark-square{width:20px;height:20px}
  .card-back .footer-band{height:24px}
  .card-back .footer-rule{bottom:29px;height:3px}
  .card-details{position:absolute;left:259px;top:55px;height:144px;border-left:1.5px solid var(--brand-blue);padding-left:11px;font-family:"Open Sans",sans-serif;font-size:12.5px;line-height:16px;color:var(--ink)}
  .card-details .name{font-weight:700;font-size:17.5px;line-height:19px;color:var(--brand-blue);margin-top:1px}
  .card-details .role{margin-bottom:13px}
  .card-details .address{margin-top:14px}
</style>
</head>
<body>

<section class="letterhead">
  <div class="wordmark"><span class="mark-square"></span>RTAVENOR</div>
  <div class="lh-contact">
    <div class="address">4187 Marlowe Ct. Linwood,<br>Vermont 27614</div>
    <div class="contact-row"><svg class="icon" width="8" height="8" viewBox="0 0 10 10"><path d="M2 0.5 3.6 2.8 2.7 3.9Q3.8 6 6 7.3L7.2 6.4 9.5 8 8.4 9.5Q2 8.5 0.5 1.6Z"/></svg>555 318 042</div>
    <div class="contact-row"><svg class="icon" width="8" height="8" viewBox="0 0 10 10"><path d="M0.5 2h9v6h-9z M0.5 2.5 5 5.6 9.5 2.5"/></svg>info@rtavenor.com</div>
    <div class="contact-row"><svg class="icon" width="8" height="8" viewBox="0 0 10 10"><circle cx="5" cy="5" r="4.5"/></svg>www.rtavenor.com</div>
  </div>

  <div class="letter">
    <div class="date">January-03-2020</div>
    <div class="recipient">Mr, Peter Lang<br>President</div>
    <div class="recipient">Harbor Corporation<br>123 Street Name, Suite# 10<br>City, State, 120023</div>
    <div class="salutation">Dear Mr, Peter</div>
    <p class="body-copy">Lorem ipsum dolor sit amet, consectetur adipiscing elit, sed do eiusmod tempor incididunt ut labore et dolore magna aliqua. Ut enim ad minim veniam, quis nostrud exercitation ullamco laboris nisi ut aliquip ex ea commodo consequat. Duis aute irure dolor in reprehenderit in voluptate velit esse cillum dolore eu fugiat nulla pariatur.</p>
    <p class="body-copy">Lorem ipsum dolor sit amet, consectetur adipiscing elit, sed do eiusmod tempor incididunt ut labore et dolore magna aliqua. Ut enim ad minim veniam, quis nostrud exercitation ullamco laboris nisi ut aliquip ex ea commodo consequat. Duis aute irure dolor in reprehenderit in voluptate velit esse cillum dolore eu fugiat nulla pariatur.</p>
    <p class="body-copy">Lorem ipsum dolor sit amet, consectetur adipiscing elit, sed do eiusmod tempor incididunt ut labore et dolore magna aliqua. Ut enim ad minim veniam, quis nostrud exercitation ullamco laboris nisi ut aliquip ex ea commodo consequat.</p>
    <p class="body-copy">Excepteur sint occaecat cupidatat non proident, sunt in culpa qui officia deserunt mollit anim id est laborum. re et dolore magnam aliquam quaerat voluptatem.</p>
    <div class="closing">Regards</div>
  </div>
  <div class="signature">Nora Ellis</div>

  <div class="footer-rule"></div>
  <div class="footer-band"></div>
</section>

<section class="card card-front">
  <div class="wordmark"><span class="mark-square"></span>RTAVENOR</div>
</section>

<section class="card card-back">
  <div class="wordmark"><span class="mark-square"></span>RTAVENOR</div>
  <div class="card-details">
    <div class="name">DANA WHITFIELD</div>
    <div class="role">Managing Director</div>
    <div class="contact-row"><svg class="icon" width="10" height="10" viewBox="0 0 10 10"><path d="M2 0.5 3.6 2.8 2.7 3.9Q3.8 6 6 7.3L7.2 6.4 9.5 8 8.4 9.5Q2 8.5 0.5 1.6Z"/></svg>555 318 042</div>
    <div class="contact-row"><svg class="icon" width="10" height="10" viewBox="0 0 10 10"><path d="M0.5 2h9v6h-9z M0.5 2.5 5 5.6 9.5 2.5"/></svg>info@rtavenor.com</div>
    <div class="contact-row"><svg class="icon" width="10" height="10" viewBox="0 0 10 10"><circle cx="5" cy="5" r="4.5"/></svg>www.rtavenor.com</div>
    <div class="address">4187 Marlowe Ct. Linwood,<br>Vermont 27614</div>
  </div>
  <div class="footer-rule"></div>
  <div class="footer-band"></div>
</section>

</body>
</html>
```